Business Card Design Project

We are rebranding an existing automotive collision repair business. The business is called dent haven. I have attached logo but I'm not tied to that. I want to leave this wide open.

I want this card to say we are professional, competent, cutting edge. We are focused on customers and use a lot of the latest technology to make the customer experience different. We sign customers in on iPads. Paperwork I signed electronically and updates are sent via text, email, logging on a website or as they wish. I want this innovation and image to come through in our cards

Target Market(s)

60%. Women 40% men. Age 35-60

Industry/Entity Type

Automotive

Requirements
Must have
• The card must have name, title, phone,email, cell, web page

```html
<!DOCTYPE html>
<html lang="en">
<head>
<meta charset="utf-8">
<title>Dent Haven – Business Card</title>
<link rel="stylesheet" href="https://fonts.googleapis.com/css2?family=Arimo:wght@400;700&family=Source+Sans+3:wght@400&display=swap">
<style>
  :root {
    --backdrop: #e6e7e9;
    --card-dark: #3a393e;
    --card-light: #a7a8ab;
    --brand-green: #5e7e34;
    --brand-lime: #9ccb45;
    --ink-dark: #222326;
    --ink-light: #ffffff;
    --note-ink: #111111;
  }
  * { margin: 0; padding: 0; box-sizing: border-box; }
  html, body { width: 1200px; height: 800px; overflow: hidden; }
  body {
    position: relative;
    background: var(--backdrop);
    font-family: "Arimo", Arial, sans-serif;
  }
  .card {
    position: absolute;
    top: 122px;
    width: 292px;
    height: 509px;
    border-radius: 14px;
    overflow: hidden;
    box-shadow: 3px 4px 4px rgba(0,0,0,0.28);
  }
  .card--front { left: 194px; background: var(--card-dark); }
  .card--back { left: 695px; background: var(--card-light); }

  .brand-band {
    position: absolute;
    left: 41px;
    top: 294px;
    width: 251px;
    height: 85px;
    background: var(--brand-green);
    border-radius: 43px 0 0 43px;
    display: flex;
    align-items: center;
    justify-content: center;
    padding-left: 18px;
  }
  .brand-name {
    font-weight: 700;
    font-size: 25px;
    color: var(--brand-lime);
    letter-spacing: -0.3px;
  }
  .front-web {
    position: absolute;
    left: 89px;
    top: 380px;
    font-size: 15px;
    color: var(--brand-green);
  }

  .accent-tab {
    position: absolute;
    left: 0;
    top: 294px;
    width: 51px;
    height: 85px;
    background: var(--brand-green);
    border-radius: 0 43px 43px 0;
  }
  .holder {
    position: absolute;
    left: 63px;
    top: 319px;
  }
  .holder-name {
    font-weight: 700;
    font-size: 19px;
    color: var(--ink-dark);
    line-height: 22px;
  }
  .holder-title {
    font-size: 15px;
    color: var(--ink-light);
    line-height: 20px;
  }
  .contact-list {
    position: absolute;
    left: 63px;
    top: 387px;
    list-style: none;
  }
  .contact-item {
    display: flex;
    align-items: center;
    height: 27px;
    font-size: 15px;
    color: var(--ink-light);
  }
  .contact-icon {
    width: 17px;
    height: 17px;
    margin-right: 13px;
    fill: none;
    stroke: var(--ink-light);
    stroke-width: 1.3;
    stroke-linecap: round;
    stroke-linejoin: round;
  }
  .presentation-note {
    position: absolute;
    left: 0;
    width: 1200px;
    top: 760px;
    text-align: center;
    font-family: "Source Sans 3", Arial, sans-serif;
    font-size: 13px;
    color: var(--note-ink);
  }
</style>
</head>
<body>
  <section class="card card--front" aria-label="Card front">
    <div class="brand-band">
      <span class="brand-name">Dent Haven</span>
    </div>
    <p class="front-web">www.denthaven.com</p>
  </section>

  <section class="card card--back" aria-label="Card back">
    <div class="accent-tab"></div>
    <div class="holder">
      <p class="holder-name">Mark Ellory</p>
      <p class="holder-title">Director</p>
    </div>
    <ul class="contact-list">
      <li class="contact-item">
        <svg class="contact-icon" viewBox="0 0 17 17"><rect x="1" y="3.5" width="15" height="10" rx="0.5"/><path d="M1 3.5l7.5 6 7.5-6"/></svg>
        abcde@denthaven.com
      </li>
      <li class="contact-item">
        <svg class="contact-icon" viewBox="0 0 17 17"><circle cx="8.5" cy="8.5" r="7"/><ellipse cx="8.5" cy="8.5" rx="3" ry="7"/><path d="M1.5 8.5h14M2.6 5h11.8M2.6 12h11.8"/></svg>
        www.denthaven.com
      </li>
      <li class="contact-item">
        <svg class="contact-icon" viewBox="0 0 17 17"><path d="M4 1.5l2.5 3-1.5 2c1 2 2.5 3.5 4.5 4.5l2-1.5 3 2.5-1.5 2.5C7.5 15.5 1.5 9.5 1.5 3z"/></svg>
        +1 (800) 555-0142
      </li>
      <li class="contact-item">
        <svg class="contact-icon" viewBox="0 0 17 17"><rect x="4.5" y="0.8" width="8" height="15.4" rx="1.2"/><path d="M7.5 13.5h2"/></svg>
        +1 (800) 555-0142
      </li>
    </ul>
  </section>

  <p class="presentation-note">*Please note all content is dummy copy • EPS is not opening, so I have used the PNG file will replace the high resolution logo when provided.</p>
</body>
</html>
```